Mental Health care Company in Washington DC

We are a new mental health care services provider in Washington DC. Please look at these sites.
https://brightwaterfamilysupport.com
https://www.quietharborinc.com
https://willowgate-dc.org/
https://www.tidepathdc.com
https://www.thelanternofdc.com

```html
<!DOCTYPE html>
<html lang="en">
<head>
<meta charset="utf-8">
<title>About Us – Lumen Health Services</title>
<link rel="stylesheet" href="https://fonts.googleapis.com/css2?family=Outfit:wght@300;400;500;600&display=swap">
<style>
:root{
  --teal:#a3d9de;
  --orange:#f5a462;
  --navy:#0d1b3d;
  --ink:#1d2433;
  --muted:#6f7480;
  --white:#ffffff;
}
*{margin:0;padding:0;box-sizing:border-box}
html,body{width:1200px;height:2746px;overflow:hidden}
body{position:relative;font-family:"Outfit",sans-serif;color:var(--ink);background:var(--white)}
.abs{position:absolute}
a{color:inherit;text-decoration:none}

/* header */
.topbar{left:0;top:0;width:1200px;height:90px;background:var(--teal)}
.call{left:92px;top:22px;display:flex;align-items:center;gap:6px;color:var(--white)}
.call-icon{width:38px;height:38px;border:1.5px solid rgba(255,255,255,.8);border-radius:8px;display:flex;align-items:center;justify-content:center}
.call small{display:block;font-size:10px;line-height:1}
.call strong{display:block;font-size:19px;font-weight:400;line-height:1.1}
.nav{left:434px;top:27px;display:flex;gap:45px;color:var(--white);font-size:15px}
.btn-appt{left:917px;top:16px;width:210px;height:45px;border-radius:23px;background:var(--orange);color:var(--white);font-size:15px;display:flex;align-items:center;justify-content:center}

/* hero */
.hero{left:0;top:80px;width:1200px;height:375px;border-radius:40px 40px 40px 0;overflow:hidden;
  background:linear-gradient(90deg,#eef3f3 0%,#dfe9ea 30%,#b8aa94 55%,#8b9b8e 75%,#c7b79a 100%)}
.hero-fade{left:0;top:0;width:520px;height:375px;background:linear-gradient(90deg,rgba(246,249,249,.95),rgba(246,249,249,0))}
.brand{left:84px;top:106px;font-size:30px;font-weight:600;line-height:34px;color:var(--navy)}
.hero-title{left:88px;top:276px;font-size:41px;font-weight:500;color:var(--ink)}

/* about */
.photo{border-radius:12px}
.ph-a{left:75px;top:520px;width:290px;height:368px;background:linear-gradient(160deg,#d9dfe2,#7a8d80 60%,#d7a64c)}
.ph-b{left:375px;top:576px;width:290px;height:360px;background:linear-gradient(160deg,#b49b83,#4a3b33 55%,#c8b7a6)}
.about-title{left:724px;top:526px;font-size:31px;font-weight:500;line-height:40px;color:#111}
.about-title span{color:var(--orange)}
.about-copy{left:723px;top:614px;width:404px;font-size:13px;line-height:21px;color:var(--muted);font-weight:300;text-align:justify}
.about-copy p+p{margin-top:10px}

/* mission */
.mission{left:75px;top:1006px;width:561px;height:303px;background:var(--teal);padding:32px 30px}
.mission h2{font-size:31px;font-weight:500;color:var(--ink);margin-bottom:10px}
.mission p{font-size:13px;line-height:21px;color:var(--ink);font-weight:300}
.mission p+p{margin-top:3px}
.ph-m{left:636px;top:1006px;width:489px;height:303px;border-radius:0 0 60px 0;background:linear-gradient(120deg,#d9d4c9,#8a7f76 45%,#495060 75%,#c7c2b6)}

/* team */
.team-title{left:0;top:1356px;width:1200px;text-align:center;font-size:31px;font-weight:500;color:var(--ink)}
.member{top:1443px;width:337px;text-align:center}
.member .ph{height:351px;border-radius:6px;background:linear-gradient(180deg,#e3e1dc,#b8bec7 55%,#5f7190)}
.member h3{margin-top:26px;font-size:18px;font-weight:500;color:#111}
.member p{margin-top:6px;font-size:13px;color:var(--muted);font-weight:300}
.socials{margin-top:15px;display:flex;justify-content:center;gap:10px}
.socials span{width:33px;height:33px;border:1.3px solid var(--ink);border-radius:50%}

/* footer */
.footer{left:0;top:1986px;width:1200px;height:681px;background:var(--teal)}
.f-brand{left:91px;top:2030px;font-size:26px;font-weight:600;line-height:30px;color:var(--white)}
.tagline{left:342px;top:2048px;font-size:20px;color:var(--white);font-weight:400}
.f-social{left:945px;top:2046px;display:flex;gap:8px}
.f-social span{width:33px;height:33px;background:var(--orange)}
.rule{left:93px;height:1px;width:1007px;background:rgba(29,36,51,.18)}
.f-head{font-size:19px;font-weight:500;color:var(--white);line-height:28px}
.field{left:103px;width:294px;border-bottom:1px solid rgba(29,36,51,.25);font-size:12px;color:var(--ink);padding-bottom:12px}
.submit{left:102px;top:2366px;width:68px;height:30px;border-radius:15px;background:var(--orange);color:var(--white);font-size:12px;display:flex;align-items:center;justify-content:center}
.links{left:509px;top:2214px;list-style:none;font-size:13px;color:var(--navy)}
.links li{height:29.5px;display:flex;align-items:center;gap:8px}
.contact{font-size:12px;color:var(--ink)}
.contact .lbl{display:flex;align-items:center;gap:6px;font-weight:300}
.contact .val{font-weight:600;color:var(--navy);margin-top:6px;line-height:18px}
.sched{left:103px;top:2425px;font-size:28px;font-weight:600;color:var(--white)}
.sched-copy{left:103px;top:2475px;width:580px;font-size:12px;line-height:18px;color:var(--ink);font-weight:300}
.call-big{left:783px;top:2411px;width:311px;height:65px;border-radius:33px;background:var(--orange);color:var(--white);font-size:28px;font-weight:600;display:flex;align-items:center;justify-content:center;gap:12px}
.disclaimer{left:100px;top:2576px;width:1000px;text-align:center;font-size:10px;line-height:16px;color:var(--ink);font-weight:300}
.bottom{left:0;top:2667px;width:1200px;height:79px;background:var(--navy);color:var(--white);font-size:12px}
.bottom .l{position:absolute;left:85px;top:30px}
.bottom .r{position:absolute;right:104px;top:30px}
</style>
</head>
<body>

<header class="abs topbar"></header>
<div class="abs call">
  <div class="call-icon">
    <svg width="20" height="20" viewBox="0 0 24 24" fill="none" stroke="#fff" stroke-width="1.6"><path d="M5 3h4l2 5-2.5 1.5a11 11 0 0 0 6 6L16 13l5 2v4a2 2 0 0 1-2 2A16 16 0 0 1 3 5a2 2 0 0 1 2-2z"/></svg>
  </div>
  <div><small>Call us today:</small><strong>202-555-0148</strong></div>
</div>
<nav class="abs nav"><a href="#">Home</a><a href="#">About</a><a href="#">Services</a><a href="#">Contact</a></nav>
<a class="abs btn-appt" href="#">Make an Appointment</a>

<section class="abs hero" role="img" aria-label="Smiling counsellor talking with a client in a bright office">
  <div class="abs hero-fade"></div>
</section>
<div class="abs brand">Lumen Health<br>Services</div>
<h1 class="abs hero-title">About Us</h1>

<div class="abs photo ph-a" role="img" aria-label="Therapist listening to a client during a session"></div>
<div class="abs photo ph-b" role="img" aria-label="Two women embracing in a support group"></div>
<h2 class="abs about-title">About Our<br><span>Lumen Health Services</span></h2>
<div class="abs about-copy">
  <p>Lorem Ipsum is simply dummy text of the printing and typesetting industry. Lorem Ipsum has been the industry's standard dummy text ever since the 1500s, when an unknown printer took a galley survived not only five centuries, but also the leap into electronic typesetting, remaining essentially unchanged. It was popularized in the 1960s with the release of Letterset sheets containing Lorem software like Aldus PageMaker including versions of Lorem Ipsum</p>
  <p>Lorem Ipsum is simply dummy text of the printing and typesetting industry. Lorem Ipsum has been the industry's standard dummy text ever since the 1500s, when an unknown printer took a galley survived not only five centuries, but also the leap into electronic typesetting, remaining essentially unchanged. It was popularized in the 1960s with the release of Letterset sheets containing Lorem software like Aldus PageMaker including versions of Lorem Ipsum</p>
</div>

<section class="abs mission">
  <h2>Our Mission</h2>
  <p>Lorem Ipsum is simply dummy text the printing and typesetting industry. Lorem Ipsum has been the industry's standard dummy text ever since the 1500s, when Lorem Ipsum is simply dummy text of the printing and typesetting industry Ipsum unknown printer took a galley of type and scrambled it to make a type specimen typesetting, remaining essentially unchanged. It was popularised in the 1960s with recently with desktop publishing software like Aldus PageMaker including versions</p>
  <p>Lorem Ipsum is simply dummy text of the printing and typesetting industry Ipsum typesetting, remaining essentially unchanged. It was popularised in the 1960s with recently with desktop publishing software like Aldus PageMaker including versions</p>
</section>
<div class="abs ph-m" role="img" aria-label="Group therapy circle seated in a bright room"></div>

<h2 class="abs team-title">Our Team</h2>
<div class="abs member" style="left:75px">
  <div class="ph" role="img" aria-label="Portrait of the founder in a suit in an office"></div>
  <h3>Martin Hale</h3><p>Founder and CEO</p>
  <div class="socials"><span aria-label="Social profile"></span><span aria-label="Social profile"></span><span aria-label="Social profile"></span></div>
</div>
<div class="abs member" style="left:431px">
  <div class="ph" role="img" aria-label="Portrait of the director seated at a desk"></div>
  <h3>Nora Bellamy</h3><p>Director</p>
  <div class="socials"><span aria-label="Social profile"></span><span aria-label="Social profile"></span><span aria-label="Social profile"></span></div>
</div>
<div class="abs member" style="left:786px">
  <div class="ph" role="img" aria-label="Portrait of the senior manager standing in an office"></div>
  <h3>Adrian Cole</h3><p>Senior Manager</p>
  <div class="socials"><span aria-label="Social profile"></span><span aria-label="Social profile"></span><span aria-label="Social profile"></span></div>
</div>

<footer class="abs footer"></footer>
<div class="abs f-brand">Lumen Health<br>Services</div>
<div class="abs tagline">Find out how we approach our client's treatment and therapy !</div>
<div class="abs f-social"><span aria-label="Social link"></span><span aria-label="Social link"></span><span aria-label="Social link"></span><span aria-label="Social link"></span></div>
<div class="abs rule" style="top:2121px"></div>

<h3 class="abs f-head" style="left:103px;top:2175px">Sign Up for Our<br>Newsletter</h3>
<div class="abs field" style="top:2254px">Enter Your Name</div>
<div class="abs field" style="top:2314px">Enter Your Email</div>
<div class="abs submit">Submit</div>

<h3 class="abs f-head" style="left:507px;top:2170px">Quick Links</h3>
<ul class="abs links">
  <li>›&nbsp;Home</li><li>›&nbsp;About</li><li>›&nbsp;Services</li><li>›&nbsp;Contact</li>
</ul>

<h3 class="abs f-head" style="left:730px;top:2171px">Get In Touch</h3>
<div class="abs contact" style="left:731px;top:2222px">
  <div class="lbl"><svg width="14" height="14" viewBox="0 0 24 24" fill="none" stroke="#1d2433" stroke-width="1.6"><path d="M5 3h4l2 5-2.5 1.5a11 11 0 0 0 6 6L16 13l5 2v4a2 2 0 0 1-2 2A16 16 0 0 1 3 5a2 2 0 0 1 2-2z"/></svg>Call Us</div>
  <div class="val">202-555-0148</div>
</div>
<div class="abs contact" style="left:920px;top:2224px">
  <div class="lbl"><svg width="14" height="14" viewBox="0 0 24 24" fill="none" stroke="#1d2433" stroke-width="1.8"><circle cx="12" cy="12" r="9"/><path d="M12 7v5l3 2"/></svg>e-mail us</div>
  <div class="val">info@lumenhealthservices.com</div>
</div>
<div class="abs contact" style="left:731px;top:2286px">
  <div class="lbl"><svg width="14" height="14" viewBox="0 0 24 24" fill="none" stroke="#1d2433" stroke-width="1.8"><circle cx="12" cy="12" r="9"/><path d="M12 7v5l3 2"/></svg>Location Hours</div>
  <div class="val">Mon – Fri: 9:00 – 6:00<br>Sat: 10 – 4:00</div>
</div>
<div class="abs contact" style="left:917px;top:2288px">
  <div class="lbl"><svg width="14" height="14" viewBox="0 0 24 24" fill="none" stroke="#1d2433" stroke-width="1.8"><path d="M12 22s7-7 7-12a7 7 0 0 0-14 0c0 5 7 12 7 12z"/><circle cx="12" cy="10" r="2.5"/></svg>Address</div>
  <div class="val">4180 Linden Street, Suite 210,<br>Washington, DC 20011</div>
</div>

<h2 class="abs sched">Schedule Your Appointment</h2>
<p class="abs sched-copy">It is a long established fact that a reader will be distracted by the readable content of a page when looking at its layout. The point of using Lorem Ipsum is that it has a more-or-less normal.</p>
<a class="abs call-big" href="#">
  <svg width="28" height="28" viewBox="0 0 24 24" fill="#fff"><path d="M5 3h4l2 5-2.5 1.5a11 11 0 0 0 6 6L16 13l5 2v4a2 2 0 0 1-2 2A16 16 0 0 1 3 5a2 2 0 0 1 2-2z"/></svg>
  1-202-555-0148
</a>
<div class="abs rule" style="top:2534px"></div>
<p class="abs disclaimer">This website is for mental health care services purposes only.It is a long established fact that a reader will be distracted by the readable content of a page when looking at its layout. The point of using Lorem Ipsum is that it has a more-or-less normal distribution of letters, as opposed to using 'Content here, content here', making it look like readable English. Many desktop publishing packages and web page editors now use Lorem Ipsum as their default model text, and a search for 'lorem ipsum' will uncover many web sites still in their infancy.</p>

<div class="abs bottom">
  <span class="l">Copyright © 2025 lumenhealthservices.com</span>
  <span class="r">Privacy Policy | Client Terms of Service</span>
</div>

</body>
</html>
```